Brightway Haul & Upkeep Services, are a company that offers a 'one stop shop' pre-move clean up a

I have already selected a logo which I would like on the front of the business cards along with phone numbers, web address and email which are:
0487650392
www.brightwayhaul.com.au
brightwayhaulandupkeep@mailbox.example

On the back of the card I would like to list some of the types of service we offer (clean - move - repairs/maintenance) which are:
CLEAN - windows, gutters, solar panels, driveways/paths, carpets.
MOVE - Small/medium size house/office moves, large item pick-up & delivery, yard clean-up and removal.
General maintenance and repairs.

I would like the blue logo on a gray background.

Thanks

```html
<!DOCTYPE html>
<html lang="en">
<head>
<meta charset="utf-8">
<title>Brightway Haul &amp; Upkeep Services – Business Card</title>
<link rel="stylesheet" href="https://fonts.googleapis.com/css2?family=Open+Sans:wght@400;600;800&display=swap">
<style>
  :root {
    --backdrop: #e4e4e4;
    --card-grey: #c9c9c9;
    --brand-blue: #1f6cb5;
    --panel-blue: #7098c1;
    --ink: #2a2a2a;
    --swoosh-dark: #1e1e1e;
    --white: #ffffff;
  }
  * { box-sizing: border-box; margin: 0; padding: 0; }
  html, body {
    width: 1200px; height: 389px; overflow: hidden;
    background: var(--backdrop);
    font-family: "Open Sans", Arial, sans-serif;
    color: var(--ink);
  }
  .sheet { position: relative; width: 1200px; height: 389px; }
  .card {
    position: absolute; top: 35px;
    width: 558px; height: 317px;
    background: var(--card-grey);
    overflow: hidden;
  }
  .card--front { left: 25px; }
  .card--back { left: 607px; }

  /* Front */
  .brand-name {
    position: absolute; left: 0; right: 0; top: 92px;
    text-align: center;
    color: var(--brand-blue);
    font-weight: 800;
    text-transform: uppercase;
    line-height: 1.1;
  }
  .brand-name__main { display: block; font-size: 44px; letter-spacing: 0.5px; }
  .brand-name__sub { display: block; font-size: 21px; margin-top: 6px; }

  .contact {
    position: absolute; left: 86px; top: 197px;
    display: flex; align-items: center;
    font-size: 14px;
  }
  .contact__phone { display: flex; align-items: center; gap: 5px; padding-right: 10px; }
  .contact__divider { width: 1px; height: 42px; background: #8a8a8a; }
  .contact__list { padding-left: 10px; display: flex; flex-direction: column; gap: 6px; }
  .contact__item { display: flex; align-items: center; gap: 6px; }
  .contact__item--web { font-size: 15px; letter-spacing: 0.5px; }
  .contact__item--mail { font-size: 12.5px; }
  .icon { width: 11px; height: 11px; flex: none; fill: var(--brand-blue); }

  .front-swoosh { position: absolute; left: 0; bottom: 0; width: 558px; height: 80px; }

  /* Back */
  .services-panel {
    position: absolute; left: 22px; top: 132px;
    width: 512px; height: 115px;
    background: var(--panel-blue);
    border-radius: 14px;
    color: var(--white);
    text-align: center;
  }
  .services-panel__title {
    margin-top: 12px;
    font-size: 21px; font-weight: 600; letter-spacing: 1.5px;
  }
  .services-panel__list { list-style: none; margin-top: 14px; font-size: 14.5px; line-height: 1.45; letter-spacing: 0.3px; }
  .back-web {
    position: absolute; left: 0; right: 0; top: 278px;
    text-align: center; font-size: 17px; letter-spacing: 1.5px;
  }
</style>
</head>
<body>
<div class="sheet">
  <section class="card card--front">
    <h1 class="brand-name">
      <span class="brand-name__main">Brightway Haul</span>
      <span class="brand-name__sub">&amp; Upkeep Services</span>
    </h1>

    <div class="contact">
      <div class="contact__phone">
        <svg class="icon" viewBox="0 0 12 12" aria-hidden="true"><path d="M2.5 0.8 L4.3 2.6 3.3 4 Q4.4 6.6 7.9 8.7 L9.3 7.7 11.2 9.5 9.6 11.2 Q4.5 10.6 0.8 2.4Z"/></svg>
        <span>0487650392</span>
      </div>
      <div class="contact__divider"></div>
      <div class="contact__list">
        <div class="contact__item contact__item--web">
          <svg class="icon" viewBox="0 0 12 12" aria-hidden="true"><circle cx="6" cy="6" r="5.5"/><path d="M0.5 6h11M6 0.5c-3 3-3 8 0 11M6 0.5c3 3 3 8 0 11" stroke="#c9c9c9" stroke-width="0.8" fill="none"/></svg>
          <span>www.brightwayhaul.com.au</span>
        </div>
        <div class="contact__item contact__item--mail">
          <svg class="icon" viewBox="0 0 12 12" aria-hidden="true"><rect x="0.5" y="2.5" width="11" height="7.5"/><path d="M0.5 2.5 6 7 11.5 2.5" stroke="#c9c9c9" stroke-width="0.9" fill="none"/></svg>
          <span>brightwayhaulandupkeep@mailbox.example</span>
        </div>
      </div>
    </div>

    <svg class="front-swoosh" viewBox="0 0 558 80" preserveAspectRatio="none" aria-hidden="true">
      <path d="M0 58 C160 26 380 12 558 14 L558 22 C380 24 190 40 0 70Z" fill="var(--swoosh-dark)"/>
      <path d="M0 72 C190 44 380 28 558 26 L558 80 L0 80Z" fill="var(--brand-blue)"/>
    </svg>
  </section>

  <section class="card card--back">
    <div class="services-panel">
      <h2 class="services-panel__title">Services we offer</h2>
      <ul class="services-panel__list">
        <li>• CLEAN • MOVE</li>
        <li>• GENERAL MAINTENANCE AND REPAIRS.</li>
      </ul>
    </div>
    <p class="back-web">www.brightwayhaul.com.au</p>
  </section>
</div>
</body>
</html>
```